QVR business card

Need a business card for a company that provides instructional design and elearning development services. The website is here: http://quorvane.studio/

I'm attaching a current logo, as well as the old business card design. While I like to keep it clean, the old design is too simplistic for my liking. The only idea I want to reuse from the old design is placing industry jargon on the back of the card, just need a better way to present it. But if you have other ideas for the back--feel free to experiment.

Please use the colors complementary to the color we have on the website. Thank you!

```html
<!DOCTYPE html>
<html lang="en">
<head>
<meta charset="utf-8">
<title>QVR business card</title>
<link href="https://fonts.googleapis.com/css2?family=Arimo:wght@400&family=Montserrat:wght@600;700&display=swap" rel="stylesheet">
<style>
  :root {
    --backdrop: #2c2c2e;
    --card: #ffffff;
    --teal: #1a9e96;
    --ink: #4a4a4a;
    --dark: #2a2a2a;
    --pale: #e4f4f4;
  }
  html, body {
    margin: 0;
    padding: 0;
    width: 1200px;
    height: 900px;
    overflow: hidden;
    background: var(--backdrop);
  }
  .canvas {
    position: relative;
    width: 1200px;
    height: 900px;
  }
  .card {
    position: absolute;
    left: 290px;
    width: 620px;
    height: 354px;
    background: var(--card);
    border-radius: 22px;
    overflow: hidden;
    box-shadow: 0 10px 24px rgba(0,0,0,0.35);
  }
  .card--back { top: 80px; }
  .card--front { top: 466px; }

  /* back side */
  .side-art {
    position: absolute;
    top: 0;
    width: 58px;
    height: 100%;
    background: linear-gradient(180deg, var(--pale), #eef8f8);
  }
  .side-art--left { left: 28px; }
  .side-art--right { right: 28px; }
  .jargon {
    position: absolute;
    left: 0;
    right: 0;
    top: 50%;
    transform: translateY(-50%);
    text-align: center;
    font-family: "Arimo", Arial, sans-serif;
    text-transform: uppercase;
  }
  .jargon__line {
    display: block;
    font-size: 25px;
    line-height: 1.2;
    letter-spacing: 2px;
    color: var(--ink);
  }
  .jargon__cta {
    display: block;
    font-family: "Montserrat", Arial, sans-serif;
    font-weight: 700;
    font-size: 33px;
    line-height: 1.25;
    letter-spacing: 1.5px;
    color: var(--teal);
  }

  /* front side */
  .holder-name {
    position: absolute;
    left: 38px;
    top: 34px;
    margin: 0;
    font-family: "Montserrat", Arial, sans-serif;
    font-weight: 700;
    font-size: 18px;
    letter-spacing: 0.5px;
    text-transform: uppercase;
    color: var(--teal);
  }
  .brand {
    position: absolute;
    left: 180px;
    top: 120px;
    display: flex;
    align-items: center;
    gap: 16px;
  }
  .brand__square {
    width: 46px;
    height: 46px;
    background: var(--teal);
  }
  .brand__name {
    font-family: "Montserrat", Arial, sans-serif;
    font-weight: 700;
    font-size: 64px;
    letter-spacing: 4px;
    color: var(--teal);
    line-height: 1;
  }
  .contact {
    position: absolute;
    right: 30px;
    bottom: 30px;
    margin: 0;
    padding: 0;
    list-style: none;
    text-align: right;
    font-family: "Montserrat", Arial, sans-serif;
    font-weight: 600;
    font-size: 14px;
    color: var(--dark);
  }
  .contact__item {
    display: flex;
    justify-content: flex-end;
    align-items: center;
    gap: 8px;
    line-height: 22px;
  }
  .contact__icon {
    width: 13px;
    height: 13px;
    fill: none;
    stroke: var(--teal);
    stroke-width: 1.6;
  }
</style>
</head>
<body>
<div class="canvas">

  <section class="card card--back" aria-label="Card back">
    <div class="side-art side-art--left" role="img" aria-label="Faint tall pen illustration along the left edge"></div>
    <div class="side-art side-art--right" role="img" aria-label="Faint tall pen illustration along the right edge"></div>
    <p class="jargon">
      <span class="jargon__line">Mobile Learning SCORM</span>
      <span class="jargon__line">Instructional Design LMS</span>
      <span class="jargon__line">MOOCs eLearning HTML5</span>
      <span class="jargon__cta">How can we help?</span>
      <span class="jargon__line">Adult Learning Theory</span>
      <span class="jargon__line">Gamification Classroom</span>
      <span class="jargon__line">xAPI Blended Learning</span>
    </p>
  </section>

  <section class="card card--front" aria-label="Card front">
    <h1 class="holder-name">Marcus Delvane</h1>
    <div class="brand">
      <span class="brand__square"></span>
      <span class="brand__name">QVR</span>
    </div>
    <ul class="contact">
      <li class="contact__item">555-014-2283
        <svg class="contact__icon" viewBox="0 0 16 16" aria-hidden="true"><path d="M4 1.5l2.5 3-1.5 1.5c.8 1.8 2.2 3.2 4 4l1.5-1.5 3 2.5-1.5 2.5C7 14 2 9 1.5 3z"/></svg>
      </li>
      <li class="contact__item">www.quorvane.studio
        <svg class="contact__icon" viewBox="0 0 16 16" aria-hidden="true"><circle cx="8" cy="8" r="6.5"/><ellipse cx="8" cy="8" rx="3" ry="6.5"/><path d="M1.5 8h13"/></svg>
      </li>
      <li class="contact__item">mdelvane@quorvane.studio
        <svg class="contact__icon" viewBox="0 0 16 16" aria-hidden="true"><rect x="1.5" y="3.5" width="13" height="9" rx="1"/><path d="M1.5 4l6.5 5 6.5-5"/></svg>
      </li>
    </ul>
  </section>

</div>
</body>
</html>
```